LinkedIn Banner Design for B2B Consulting Firm

Take the already developed logo (attached) and incorporate it into a creative banner design for placement on LinkedIn (the social media platform targeting business users). The banner will be used on the firm's company profile page on LinkedIn (not yet created).

```html
<!DOCTYPE html>
<html lang="en">
<head>
<meta charset="utf-8">
<title>Fractional Marketing Services – LinkedIn Banner</title>
<link rel="stylesheet" href="https://fonts.googleapis.com/css2?family=Lato:wght@400;700&display=swap">
<style>
  :root {
    --backdrop: #dcd9d9;
    --backdrop-light: #e6e4e4;
    --banner-white: #ffffff;
    --brand-green: #46634b;
    --text-light: #ffffff;
    --photo-light: #e9eef2;
    --photo-mid: #b9c3cc;
    --photo-dark: #6f7d8a;
  }
  * { margin: 0; padding: 0; box-sizing: border-box; }
  html, body {
    width: 1200px;
    height: 470px;
    overflow: hidden;
  }
  body {
    position: relative;
    background: radial-gradient(ellipse at center, var(--backdrop-light) 0%, var(--backdrop) 75%);
    font-family: "Lato", Arial, sans-serif;
  }
  .banner {
    position: absolute;
    left: 60px;
    top: 144px;
    width: 1080px;
    height: 183px;
    background: var(--banner-white);
  }
  .banner__band {
    position: absolute;
    left: 0;
    top: 32px;
    width: 711px;
    height: 119px;
    background: var(--brand-green);
  }
  .banner__headline {
    position: absolute;
    left: 332px;
    top: 13px;
    color: var(--text-light);
    font-weight: 700;
    font-size: 30.5px;
    line-height: 31px;
    letter-spacing: 0.1px;
    white-space: nowrap;
  }
  .banner__audience {
    position: absolute;
    left: 332px;
    top: 85px;
    color: var(--text-light);
    font-weight: 400;
    font-size: 11.5px;
    white-space: nowrap;
  }
  .banner__photo {
    position: absolute;
    left: 711px;
    top: 0;
    width: 369px;
    height: 183px;
    background: linear-gradient(100deg, var(--photo-light) 0%, var(--photo-mid) 45%, var(--photo-dark) 70%, var(--photo-light) 100%);
  }
</style>
</head>
<body>
  <section class="banner">
    <div class="banner__band">
      <h1 class="banner__headline">Fractional&nbsp; Marketing<br>Services to B2B clients</h1>
      <p class="banner__audience">Private Equity Firms, Family Offices, Investment Banks</p>
    </div>
    <div class="banner__photo" role="img" aria-label="Photo of a smiling business team gathered around a table with a laptop and papers in a bright office"></div>
  </section>
</body>
</html>
```